Brell Stone Company Business Cards

Front and Back Business Card - logo and text setup - cool design. I need workable photoshop or illustrator files so I can setup each employee card with design that is created
Updates

Hi everyone, thank you for the great entries. Please no more white and blue cards - there are so many already - black and silver only now please. thanks!

Target Market(s)

Construction Industry - Facility Managers

Industry/Entity Type

Construction

Contact Information for Business Card

I really like contemporary simplistic looks - clean neat....not opposed to seeing some black backrounds

Requirements
Must have
• Logo/website address with design on front only - www.brellstone-example.com (logo attached)
• Back:
• Name/Title/Company Address/Phone/email address
Nice to have
• Cool design
Should not have
• Nothing gimmicky like Fire or Water - since we are a Fire Protection company - it has all been done

```html
<!DOCTYPE html>
<html lang="en">
<head>
<meta charset="utf-8">
<title>Brell Stone Company – Business Cards</title>
<link rel="stylesheet" href="https://fonts.googleapis.com/css2?family=Open+Sans:wght@400;600;700&display=swap">
<style>
  :root {
    --page-bg: #1b1b1d;
    --card-top: #3a3a3d;
    --card-bottom: #242426;
    --card-edge: #141415;
    --text-light: #f2f2f2;
    --brand-blue: #2f5597;
  }
  * { margin: 0; padding: 0; box-sizing: border-box; }
  html, body {
    width: 1200px;
    height: 874px;
    overflow: hidden;
    background: var(--page-bg);
  }
  .canvas {
    position: relative;
    width: 1200px;
    height: 874px;
    display: flex;
    flex-direction: column;
    align-items: center;
    justify-content: center;
    gap: 40px;
    font-family: "Open Sans", Arial, sans-serif;
  }
  .card {
    width: 620px;
    height: 354px;
    border-radius: 22px;
    background: radial-gradient(ellipse at 55% 40%, var(--card-top), var(--card-bottom) 75%);
    border: 1px solid var(--card-edge);
    box-shadow: 0 12px 30px rgba(0, 0, 0, 0.55);
    display: flex;
    flex-direction: column;
    align-items: center;
    justify-content: center;
  }
  .brand {
    display: flex;
    align-items: center;
    gap: 16px;
  }
  .brand-mark {
    width: 26px;
    height: 26px;
    background: var(--brand-blue);
  }
  .brand-name {
    font-size: 56px;
    font-weight: 700;
    color: var(--brand-blue);
    letter-spacing: -0.5px;
  }
  .card-back {
    color: var(--text-light);
    text-align: center;
    padding-top: 60px;
  }
  .person {
    font-size: 21px;
    font-weight: 600;
    margin-bottom: 6px;
  }
  .person .role {
    font-size: 16px;
    font-weight: 400;
  }
  .contact-line {
    font-size: 14px;
    line-height: 22px;
  }
  .website {
    font-size: 14px;
    letter-spacing: 4px;
  }
</style>
</head>
<body>
  <main class="canvas">
    <section class="card card-front" aria-label="Card front">
      <div class="brand">
        <span class="brand-mark"></span>
        <span class="brand-name">Brell Stone</span>
      </div>
    </section>
    <section class="card card-back" aria-label="Card back">
      <p class="person">Daniel Moore <span class="role">- CEO/Founder</span></p>
      <p class="contact-line">48 Harbor Point Road, Ridgeview, NY 10000</p>
      <p class="contact-line">P. (555) 010-2040 F. (555) 010-2041 E. info@brellstone-example.com</p>
      <p class="website">www.brellstone-example.com</p>
    </section>
  </main>
</body>
</html>
```